Business Card Design Project

Business Card
We are rebranding with a new logo
Industry/Entity Type
Business
Contact Information for Business Card
Dennis Morvale +61 487215963 dennis@quorv.com.au P.O. Box 872 Fernlow QLD 4309
Requirements
Must have
- Logo

```html
<!DOCTYPE html>
<html lang="en">
<head>
<meta charset="UTF-8">
<title>Quorv International – Business Card</title>
<link rel="stylesheet" href="https://fonts.googleapis.com/css2?family=Rajdhani:wght@400;500;700&display=swap">
<style>
  :root {
    --page-bg: #ececec;
    --card-white: #ffffff;
    --navy: #1d3b64;
    --ink: #1a1a1a;
    --brand-blue: #1f7fc4;
    --text-light: #f2f5f9;
  }
  * { box-sizing: border-box; margin: 0; padding: 0; }
  html, body {
    width: 1200px;
    height: 800px;
    overflow: hidden;
    background: var(--page-bg);
    font-family: "Rajdhani", sans-serif;
  }
  .canvas {
    width: 1200px;
    height: 800px;
    display: flex;
    align-items: center;
    justify-content: center;
  }
  .business-card {
    position: relative;
    width: 900px;
    height: 514px;
    background: var(--card-white);
    box-shadow: 0 10px 30px rgba(0, 0, 0, 0.12);
    overflow: hidden;
  }
  .brand-panel {
    position: absolute;
    left: 0; top: 0;
    width: 390px;
    height: 100%;
  }
  .brand-mark {
    position: absolute;
    left: 70px;
    top: 120px;
    display: flex;
    align-items: center;
    gap: 14px;
  }
  .brand-dot {
    width: 34px;
    height: 34px;
    border-radius: 50%;
    background: var(--brand-blue);
  }
  .brand-name {
    font-weight: 700;
    font-size: 40px;
    letter-spacing: 0.12em;
    color: var(--ink);
    text-transform: uppercase;
    line-height: 1;
  }
  .brand-name small {
    display: block;
    font-size: 17px;
    letter-spacing: 0.32em;
    margin-top: 6px;
  }
  .email {
    position: absolute;
    right: 30px;
    bottom: 74px;
    font-size: 18px;
    font-weight: 500;
    letter-spacing: 0.28em;
    color: var(--ink);
    white-space: nowrap;
  }
  .contact-panel {
    position: absolute;
    left: 390px; top: 0;
    width: 510px;
    height: 100%;
    background: var(--navy);
    color: var(--text-light);
  }
  .person-name {
    position: absolute;
    left: 70px;
    top: 110px;
    font-weight: 700;
    font-size: 30px;
    letter-spacing: 0.08em;
    text-transform: uppercase;
  }
  .contact-list {
    position: absolute;
    left: 70px;
    top: 300px;
    list-style: none;
    font-size: 20px;
    font-weight: 500;
    letter-spacing: 0.06em;
  }
  .contact-list li {
    display: flex;
    align-items: center;
    gap: 16px;
    margin-bottom: 16px;
  }
  .contact-list svg {
    width: 20px;
    height: 20px;
    fill: var(--text-light);
    flex: none;
  }
</style>
</head>
<body>
<main class="canvas">
  <article class="business-card">
    <section class="brand-panel">
      <div class="brand-mark">
        <span class="brand-dot" aria-hidden="true"></span>
        <span class="brand-name">Quorv<small>International</small></span>
      </div>
      <p class="email">dennis@quorv.com.au</p>
    </section>
    <section class="contact-panel">
      <h1 class="person-name">Dennis Morvale</h1>
      <ul class="contact-list">
        <li>
          <svg viewBox="0 0 24 24" aria-hidden="true"><path d="M6.6 10.8a15.1 15.1 0 0 0 6.6 6.6l2.2-2.2a1 1 0 0 1 1-.25 11.4 11.4 0 0 0 3.6.57 1 1 0 0 1 1 1V20a1 1 0 0 1-1 1A17 17 0 0 1 3 4a1 1 0 0 1 1-1h3.5a1 1 0 0 1 1 1c0 1.25.2 2.45.57 3.57a1 1 0 0 1-.25 1z"/></svg>
          <span>+61 487215963</span>
        </li>
        <li>
          <svg viewBox="0 0 24 24" aria-hidden="true"><path d="M12 3 2 12h3v8h5v-5h4v5h5v-8h3z"/></svg>
          <span>P.O. Box 872 Fernlow QLD 4309</span>
        </li>
      </ul>
    </section>
  </article>
</main>
</body>
</html>
```